Dental specialist needs a sharp looking letterhead

I am looking for a letterhead to be used to send letters and communication between myself (a dental specialist) and other dentists.
My office is a state of the art dental specialty office.
I need to letterhead to also state:
Bertram L. Oswick DDS
2748 Tollard Avenue, Suite K
West Tollard, NY 14391
(716)392-5061
fax: (716)392-5087
oswickroot.com (**this email address may change)

i included my logo designs.
thank you

Target Market(s)

dentists

Industry/Entity Type

Communication

Requirements
Must have
• the included logo, whether the vertical or horizontal versions

```html
<!DOCTYPE html>
<html lang="en">
<head>
<meta charset="utf-8">
<title>Tollard Endodontics P.C. – Letterhead</title>
<link href="https://fonts.googleapis.com/css2?family=Open+Sans:wght@400;600;700&display=swap" rel="stylesheet">
<style>
  :root {
    --backdrop: #1c1c1c;
    --paper: #ffffff;
    --brand-blue: #1fa9e1;
    --brand-green: #8dc63f;
    --ink: #3a3a3a;
    --ink-soft: #666666;
    --wash-blue: rgba(31, 169, 225, 0.10);
    --wash-green: rgba(141, 198, 63, 0.08);
  }
  * { box-sizing: border-box; margin: 0; padding: 0; }
  html, body {
    width: 1200px;
    height: 750px;
    overflow: hidden;
    background: var(--backdrop);
    font-family: "Open Sans", Arial, sans-serif;
  }
  .letterhead {
    position: absolute;
    left: 335px;
    top: 32px;
    width: 530px;
    height: 686px;
    background: var(--paper);
    box-shadow: 0 10px 30px rgba(0,0,0,0.5);
    overflow: hidden;
  }
  .brand-wash {
    position: absolute;
    right: -40px;
    top: 250px;
    width: 260px;
    height: 300px;
    background:
      radial-gradient(ellipse at 40% 45%, var(--wash-blue) 0%, rgba(31,169,225,0) 65%),
      radial-gradient(ellipse at 70% 75%, var(--wash-green) 0%, rgba(141,198,63,0) 60%);
  }
  .sender {
    position: absolute;
    left: 40px;
    top: 42px;
    width: 190px;
  }
  .practice-mark {
    display: flex;
    align-items: center;
    gap: 7px;
  }
  .practice-mark__dot {
    width: 16px;
    height: 16px;
    border-radius: 50%;
    background: var(--brand-blue);
    flex: none;
  }
  .practice-mark__name {
    font-size: 10px;
    font-weight: 700;
    color: var(--ink);
    letter-spacing: 0.04em;
    line-height: 1.15;
  }
  .doctor {
    margin-top: 8px;
    text-align: right;
  }
  .doctor__name {
    font-size: 10px;
    color: var(--brand-blue);
    letter-spacing: 0.14em;
  }
  .doctor__degree {
    font-size: 8px;
    color: var(--brand-green);
    letter-spacing: 0.08em;
  }
  .contact {
    margin-top: 10px;
    text-align: right;
    font-size: 7.5px;
    line-height: 1.6;
    color: var(--ink);
    font-style: normal;
  }
  .contact__label { color: var(--brand-blue); }
  .letter-body {
    position: absolute;
    left: 235px;
    top: 215px;
    width: 260px;
    font-size: 6.5px;
    line-height: 1.55;
    color: var(--ink-soft);
  }
  .letter-body p { margin-bottom: 9px; }
  .letter-body .closing { margin-top: 40px; margin-left: 70px; }
  .website {
    position: absolute;
    right: 36px;
    bottom: 34px;
    font-size: 9px;
    letter-spacing: 0.42em;
    color: var(--brand-blue);
  }
</style>
</head>
<body>
  <main class="letterhead">
    <div class="brand-wash" role="img" aria-label="Faint brand-colour wash in blue and green"></div>

    <header class="sender">
      <div class="practice-mark">
        <span class="practice-mark__dot"></span>
        <span class="practice-mark__name">TOLLARD<br>Endodontics P.C.</span>
      </div>
      <div class="doctor">
        <div class="doctor__name">Bertram L. Oswick</div>
        <div class="doctor__degree">D.D.S</div>
      </div>
      <address class="contact">
        <span class="contact__label">Address:</span> 2748 Tollard Avenue<br>
        Suite K West Tollard, NY 14391<br>
        <span class="contact__label">Phone:</span> (716)392-5061<br>
        <span class="contact__label">Fax:</span> (716)392-5087
      </address>
    </header>

    <section class="letter-body">
      <p>Lorem Ipsum,</p>
      <p>Lorem ipsum dolor sit amet, consectetuer adipiscing elit. Nam cursus. Morbi ut mi. Nullam enim leo, egestas id, condimentum at, laoreet mattis, massa. Sed eleifend nonummy diam. Praesent mauris ante, elementum et, bibendum at, posuere sit amet, nibh. Duis tincidunt lectus quis dui viverra vestibulum. Suspendisse vulputate aliquam dui. Nulla elementum dui ut augue.</p>
      <p>Aliquam vehicula mi at mauris. Maecenas placerat, nisl at consequat rhoncus, sem nunc gravida justo, quis eleifend arcu velit quis lacus. Morbi magna magna, tincidunt a, mattis non, imperdiet vitae, tellus.</p>
      <p>Mauris nunc quam, venenatis nec, euismod sit amet, egestas placerat, est. Pellentesque habitant morbi tristique senectus et netus et malesuada fames ac turpis egestas. Cras id elit. Integer quis urna.</p>
      <p>Aliquam vehicula mi at mauris. Maecenas placerat, nisl at consequat rhoncus, sem nunc gravida justo, quis eleifend arcu velit quis lacus. Morbi magna magna, tincidunt a, mattis non, imperdiet vitae, tellus.</p>
      <p>Mauris nunc quam, venenatis nec, euismod sit amet, egestas placerat, est. Pellentesque habitant morbi tristique senectus et netus et malesuada fames ac turpis egestas. Cras id elit. Integer quis urna.</p>
      <p class="closing">Sincerely,</p>
    </section>

    <footer class="website">www.oswickroot.com</footer>
  </main>
</body>
</html>
```